Barrister at Law needs Business Card Design

Need a business card design for Barrister at Law. Double sided. Simple Neil Thorsby and Barrister at Law on one side with contact details on the other side. I would like a professional design using Black or Platinum. Details on reverse side would include qualifications - Bcom-Llb and Acc Spec Commercial Litigation. I have attached the logo. Contact details would include address/ Po Box/ Phone/Fax/Mobile/email. I would like to use raised print or spot gloss.

```html
<!DOCTYPE html>
<html lang="en">
<head>
<meta charset="utf-8">
<title>Neil Thorsby, Barrister at Law: Business Cards</title>
<link rel="stylesheet" href="https://fonts.googleapis.com/css2?family=Cinzel:wght@700&family=Open+Sans:wght@400;600&display=swap">
<style>
  :root {
    --stage: #3a3431;
    --card-black: #141414;
    --card-black-edge: #202020;
    --silver-light: #ffffff;
    --silver-dark: #9a9a9a;
    --law-blue: #1f8ee0;
    --law-blue-dark: #0d5fa8;
    --card-blue: #1a80d2;
    --card-blue-deep: #1470bd;
    --ink-white: #ffffff;
    --ink-soft: #e3f0fb;
  }
  * { margin: 0; padding: 0; box-sizing: border-box; }
  html, body { width: 1200px; height: 844px; overflow: hidden; }
  body {
    background: var(--stage);
    display: flex;
    align-items: center;
    justify-content: center;
    gap: 60px;
  }
  .card {
    width: 525px;
    height: 300px;
    border-radius: 4px;
    position: relative;
    overflow: hidden;
    box-shadow: 0 14px 30px rgba(0,0,0,0.45);
  }

  /* Front */
  .card-front {
    background: radial-gradient(ellipse at 40% 40%, var(--card-black-edge), var(--card-black));
    display: flex;
    flex-direction: column;
    align-items: center;
    justify-content: center;
    gap: 14px;
    font-family: "Cinzel", "Trajan Pro", serif;
    font-weight: 700;
    letter-spacing: 1px;
  }
  .holder-name {
    font-size: 38px;
    background: linear-gradient(180deg, var(--silver-light) 30%, var(--silver-dark) 100%);
    -webkit-background-clip: text;
    background-clip: text;
    color: transparent;
    filter: drop-shadow(1px 2px 1px rgba(0,0,0,0.8));
  }
  .holder-title {
    font-size: 40px;
    background: linear-gradient(180deg, #5ab4f5 20%, var(--law-blue) 55%, var(--law-blue-dark) 100%);
    -webkit-background-clip: text;
    background-clip: text;
    color: transparent;
    filter: drop-shadow(1px 2px 1px rgba(0,0,0,0.8));
  }

  /* Back */
  .card-back {
    background: linear-gradient(135deg, var(--card-blue) 0%, var(--card-blue-deep) 100%);
    font-family: "Open Sans", Arial, sans-serif;
    color: var(--ink-white);
    padding: 58px 0 0 46px;
  }
  .firm-mark {
    position: absolute;
    right: 28px;
    top: 36px;
    display: flex;
    align-items: center;
    gap: 10px;
    font-size: 17px;
    font-weight: 600;
    color: rgba(255,255,255,0.22);
  }
  .firm-mark .dot {
    width: 14px; height: 14px; border-radius: 50%;
    background: rgba(255,255,255,0.22);
  }
  .back-name { font-size: 17px; font-weight: 600; line-height: 1.2; }
  .back-name .quals { font-size: 12px; font-weight: 600; }
  .speciality { font-size: 12.5px; color: var(--ink-soft); margin-top: 1px; }
  .address { font-size: 12.5px; color: var(--ink-soft); margin-top: 26px; line-height: 1.3; }
  .contacts { list-style: none; margin-top: 20px; margin-left: 36px; }
  .contacts li {
    display: flex; align-items: center; gap: 8px;
    font-size: 13px; line-height: 1.35;
  }
  .contacts svg { width: 10px; height: 10px; fill: var(--ink-white); flex: none; }
</style>
</head>
<body>
  <section class="card card-front" aria-label="Card front">
    <h1 class="holder-name">NEIL THORSBY</h1>
    <p class="holder-title">BARRISTER AT LAW</p>
  </section>

  <section class="card card-back" aria-label="Card back">
    <div class="firm-mark"><span class="dot"></span>Thorsby Chambers</div>
    <p class="back-name">Neil Thorsby <span class="quals">Bcom, LLB</span></p>
    <p class="speciality">Acc Spec Commercial Litigation</p>
    <p class="address">12345, Address Goes Here<br>Country Name, 123456</p>
    <ul class="contacts">
      <li><svg viewBox="0 0 10 10"><path d="M1 3c0-1 1-2 4-2s4 1 4 2v1H7V3H3v1H1zM2 5h6l1 4H1z"/></svg>(044)-456-7890</li>
      <li><svg viewBox="0 0 10 10"><path d="M3 0h4v3H3zM1 3h8v7H1zM3 5h1v1H3zm2 0h1v1H5zm2 0h1v1H7zM3 7h1v1H3zm2 0h1v1H5zm2 0h1v1H7z"/></svg>123-456-7890</li>
      <li><svg viewBox="0 0 10 10"><path d="M0 2h10v6H0zM1 3l4 3 4-3v-.2L5 5 1 2.8z" fill-rule="evenodd"/></svg>info@youremail.com</li>
      <li><svg viewBox="0 0 10 10"><path d="M2 5l3-3a2 2 0 013 3l-1 1-1-1 1-1a.8.8 0 00-1-1L3 6zM8 5L5 8a2 2 0 01-3-3l1-1 1 1-1 1a.8.8 0 001 1l3-3z"/></svg>www.website.com</li>
    </ul>
  </section>
</body>
</html>
```